Business Card Design Project

We are an incubator company that helps young entrepreneur to launch new ideas into the market. We will be targeting investors or likewise; Angels, young entrepreneurs and technopreneurs.

Our logo is being tasked by pixelhive to design, therefore there is no logo for now.
You can us Lanternfield Pte Ltd as the logo for the time being.

Please let us have some versions of modern and yet professional designs; for words, you can indicate e.g (address), (Title)

thanks

Target Market(s)

young entrepreneurs
angels, investors

Industry/Entity Type

Business

Colors
3176b5
ffffff

Requirements
Must have
• able to project out our name; Lanternfield
Should not have
• Nothing childish or cartoon

```html
<!DOCTYPE html>
<html lang="en">
<head>
<meta charset="utf-8">
<title>Lanternfield Business Card</title>
<link rel="stylesheet" href="https://fonts.googleapis.com/css2?family=Oxygen:wght@400;700&display=swap">
<style>
  :root {
    --page-bg: #eceef1;
    --brand-blue: #3176b5;
    --blue-light: #22a3e0;
    --blue-mid: #1e88d0;
    --blue-deep: #1f5fa3;
    --white: #ffffff;
    --paper: #eef0f2;
    --silver: #c9ccd1;
    --card-shadow: rgba(20, 30, 50, 0.35);
  }
  * { margin: 0; padding: 0; box-sizing: border-box; }
  html, body {
    width: 1200px; height: 900px; overflow: hidden;
    background: var(--page-bg);
    font-family: "Oxygen", Arial, sans-serif;
  }
  .canvas { position: relative; width: 1200px; height: 900px; }
  .card {
    position: absolute; top: 306px;
    width: 500px; height: 288px;
    box-shadow: 4px 6px 10px var(--card-shadow);
    overflow: hidden;
  }
  .card-front {
    left: 70px;
    background: linear-gradient(135deg, var(--blue-mid) 0%, var(--blue-light) 100%);
  }
  .card-back { left: 630px; background: var(--blue-mid); }

  .brand {
    display: flex; align-items: center; gap: 10px;
    position: absolute; font-weight: 700; letter-spacing: 1px;
    text-transform: uppercase; line-height: 1;
    white-space: nowrap;
  }
  .brand-mark { flex: none; }
  .card-front .brand {
    left: 0; right: 0; top: 126px; justify-content: center;
    font-size: 32px; color: var(--silver);
  }
  .card-front .brand-mark { background: var(--silver); width: 22px; height: 22px; }
  .card-back .brand {
    left: 28px; top: 186px; font-size: 25px; color: var(--brand-blue);
  }
  .card-back .brand-mark { background: var(--brand-blue); width: 17px; height: 17px; }

  .back-shapes { position: absolute; inset: 0; width: 100%; height: 100%; }

  .contact {
    position: absolute; left: 312px; top: 36px; color: var(--white);
  }
  .contact-name { font-size: 21px; font-weight: 400; margin-bottom: 14px; white-space: nowrap; }
  .contact-row {
    display: flex; align-items: center; gap: 9px;
    font-size: 10px; height: 18px; margin-bottom: 7px;
  }
  .contact-row svg { width: 11px; height: 11px; flex: none; }
</style>
</head>
<body>
<main class="canvas">

  <section class="card card-front" aria-label="Card front">
    <div class="brand"><span class="brand-mark"></span>Lanternfield</div>
  </section>

  <section class="card card-back" aria-label="Card back">
    <svg class="back-shapes" viewBox="0 0 500 288" preserveAspectRatio="none" aria-hidden="true">
      <defs>
        <linearGradient id="panelGrad" x1="0" y1="0" x2="1" y2="1">
          <stop offset="0" stop-color="#f6f7f8"/>
          <stop offset="1" stop-color="#e4e6e9"/>
        </linearGradient>
      </defs>
      <polygon points="0,0 392,228 0,262" fill="url(#panelGrad)"/>
      <polygon points="0,262 392,228 500,288 0,288" fill="#2068ae"/>
    </svg>

    <div class="contact">
      <div class="contact-name">Name Surname</div>
      <div class="contact-row">
        <svg viewBox="0 0 12 12"><path d="M2 1 L4 1 L5 4 L3.6 5 Q5 7.5 7 8.4 L8 7 L11 8 L11 10 Q10 11 8.5 11 Q2 9 1 2.5 Q1 1 2 1Z" fill="#fff"/></svg>
        <span>000 000 000</span>
      </div>
      <div class="contact-row">
        <svg viewBox="0 0 12 12"><rect x="3" y="0.5" width="6" height="11" rx="1" fill="none" stroke="#fff"/><rect x="4.5" y="9" width="3" height="1" fill="#fff"/></svg>
        <span>000 000 000</span>
      </div>
      <div class="contact-row">
        <svg viewBox="0 0 12 12"><rect x="0.5" y="2.5" width="11" height="7" fill="none" stroke="#fff"/><path d="M0.5 2.5 L6 6.5 L11.5 2.5" fill="none" stroke="#fff"/></svg>
        <span>email@website.com</span>
      </div>
      <div class="contact-row">
        <svg viewBox="0 0 12 12"><circle cx="6" cy="6" r="5.3" fill="none" stroke="#fff"/><ellipse cx="6" cy="6" rx="2.3" ry="5.3" fill="none" stroke="#fff"/><path d="M0.7 6 H11.3" stroke="#fff"/></svg>
        <span>www.website.com</span>
      </div>
    </div>

    <div class="brand"><span class="brand-mark"></span>Lanternfield</div>
  </section>

</main>
</body>
</html>
```